New Business Card Design Project

We require a business card design for Vexalund, a newly established Indian company.
Our focus is on the development, manufacturing, and export of a diverse array of pharmaceutical products on a global scale. The card should convey a professional appearance, as our primary markets are in Africa, China, and Southeast Asian nations.
We envision a two-sided business card, with the reverse side dedicated to a logo set against a solid color or an elegantly designed pattern. The corners should be rounded. We would appreciate seeing both horizontal and vertical design options. We trust the designer to utilize their expertise in creating this design.

The content for the business card is included in the attached Word file.

Target Market(s)

Our primary markets are in Africa, China, and Southeast Asian, Latin America, Maldives, Sri Lanka

Industry/Entity Type

Pharmaceutical Manufacturing and Export

Contact Information for Business Card

Colors

Designer to choose colors to be used in the design.

Requirements
Must have
• The reverse side of the business card features solely the logo along with the tagline, "Healing Made Pure."
Should not have
• The logo should not exceed two instances, encompassing both the front and back sides of the card.

```html
<!DOCTYPE html>
<html lang="en">
<head>
<meta charset="utf-8">
<title>Vexalund Business Card</title>
<link rel="stylesheet" href="https://fonts.googleapis.com/css2?family=Montserrat:wght@700;800&family=Arimo:wght@400&display=swap">
<style>
  :root {
    --stage: #2a2a2a;
    --card-light: #ffffff;
    --card-dark: #333333;
    --brand-blue: #29a8e0;
    --accent-red: #ef5a45;
    --ink-grey: #5a5a5a;
    --ink-light: #f2f2f2;
  }
  * { margin: 0; padding: 0; box-sizing: border-box; }
  html, body {
    width: 1200px; height: 689px; overflow: hidden;
    background: var(--stage);
  }
  .stage {
    position: relative; width: 1200px; height: 689px;
  }
  .card {
    position: absolute; top: 196px;
    width: 520px; height: 297px;
    border-radius: 22px;
    box-shadow: 0 10px 30px rgba(0,0,0,0.35);
    overflow: hidden;
  }
  .card--back {
    left: 50px; background: var(--card-light);
    display: flex; flex-direction: column; align-items: center; justify-content: center;
  }
  .brand-name {
    font-family: "Montserrat", sans-serif; font-weight: 800;
    color: var(--brand-blue); letter-spacing: 0.5px;
    white-space: nowrap;
  }
  .card--back .brand-name { font-size: 54px; line-height: 1; }
  .tagline {
    margin-top: 14px;
    font-family: "Arimo", sans-serif; font-size: 15px;
    color: var(--ink-grey); letter-spacing: 0.3px;
  }
  .card--front {
    left: 630px; background: var(--card-dark);
    padding: 46px 40px;
  }
  .card--front .brand-name { font-size: 40px; line-height: 1; }
  .person-name {
    margin-top: 22px;
    font-family: "Montserrat", sans-serif; font-weight: 700;
    font-size: 21px; color: var(--brand-blue);
  }
  .person-role {
    font-family: "Arimo", sans-serif; font-size: 14px;
    color: var(--accent-red); margin-top: 2px;
  }
  .address {
    margin-top: 14px;
    font-family: "Arimo", sans-serif; font-size: 13px; line-height: 1.35;
    color: var(--ink-light);
  }
  .contact-list { list-style: none; margin-top: 12px; }
  .contact-item {
    display: flex; align-items: center; gap: 10px;
    font-family: "Arimo", sans-serif; font-size: 13px; line-height: 1.6;
    color: var(--ink-light);
  }
  .contact-icon { width: 12px; height: 12px; flex: none; }
  .contact-icon path, .contact-icon circle, .contact-icon rect { fill: var(--brand-blue); }
</style>
</head>
<body>
<main class="stage">
  <section class="card card--back" aria-label="Card back">
    <div class="brand-name">Vexalund</div>
    <p class="tagline">Healing Made Pure</p>
  </section>

  <section class="card card--front" aria-label="Card front">
    <div class="brand-name">Vexalund</div>
    <p class="person-name">Ravin K. Sathe</p>
    <p class="person-role">CEO</p>
    <p class="address">14, Nilgiri Lane,Pune<br>411001, India</p>
    <ul class="contact-list">
      <li class="contact-item">
        <svg class="contact-icon" viewBox="0 0 24 24" aria-hidden="true"><path d="M6.6 10.8a15.1 15.1 0 0 0 6.6 6.6l2.2-2.2a1 1 0 0 1 1-.25 11.4 11.4 0 0 0 3.6.57 1 1 0 0 1 1 1V20a1 1 0 0 1-1 1A17 17 0 0 1 3 4a1 1 0 0 1 1-1h3.5a1 1 0 0 1 1 1c0 1.25.2 2.45.57 3.57a1 1 0 0 1-.25 1z"/></svg>
        +919800017342
      </li>
      <li class="contact-item">
        <svg class="contact-icon" viewBox="0 0 24 24" aria-hidden="true"><path d="M2 5h20v14H2z M4 7v.5l8 5 8-5V7l-8 5z"/></svg>
        rsathe@vexalund.com
      </li>
      <li class="contact-item">
        <svg class="contact-icon" viewBox="0 0 24 24" aria-hidden="true"><circle cx="12" cy="12" r="10"/></svg>
        www.vexalund.com
      </li>
    </ul>
  </section>
</main>
</body>
</html>
```